Awesome new dental practice requires a New Letterhead design

We would like a new letterhead design to align with our new business branding & business cards. I have uploaded all the logos & current business card details that can be used. The new website can be viewed here https://velortis.com.au

Other useful details: Font Poppins
Colour Palettes:
Dark Pink #c45389
Light Pink: #e83e8c
Black

Please let me know if you have any questions or require anything else.

Dental

• Poppins

```html
<!DOCTYPE html>
<html lang="en">
<head>
<meta charset="utf-8">
<title>Velortis Letterhead</title>
<link href="https://fonts.googleapis.com/css2?family=Poppins:wght@400;500;600;700&family=Open+Sans:wght@400;600&display=swap" rel="stylesheet">
<style>
  :root {
    --backdrop: #b3b3b3;
    --paper: #fafafa;
    --ink: #111111;
    --body-text: #5c5c5c;
    --pink-dark: #c45389;
    --pink-band: #d04a88;
    --pink-light: #e83e8c;
    --pink-soft: #f7a9cc;
  }
  * { margin: 0; padding: 0; box-sizing: border-box; }
  html, body { width: 1200px; height: 1001px; overflow: hidden; }
  body { background: var(--backdrop); position: relative; font-family: 'Open Sans', sans-serif; }

  .letterhead {
    position: absolute; left: 287px; top: 58px;
    width: 625px; height: 884px;
    background: var(--paper);
    overflow: hidden;
  }

  .brand {
    position: absolute; right: 59px; top: 76px; text-align: right;
    font-family: 'Poppins', sans-serif;
  }
  .brand-name {
    font-size: 38px; font-weight: 600; color: var(--ink);
    line-height: 1; letter-spacing: -0.5px;
  }
  .brand-tagline {
    margin-top: 6px; font-size: 11px; font-weight: 600;
    letter-spacing: 2.3px; color: var(--ink);
  }

  .letter-body {
    position: absolute; left: 59px; top: 192px; width: 507px;
    font-size: 9.15px; line-height: 16px; color: var(--body-text);
  }
  .salutation { margin-bottom: 32px; }
  .letter-body p.paragraph { text-align: justify; margin-bottom: 16px; }

  .sign-off { position: absolute; left: 59px; top: 574px; color: var(--body-text); }
  .sign-off .name-label { font-size: 9.4px; font-weight: 600; color: #444; }
  .signature {
    width: 152px; height: 32px; margin: 8px 0 7px;
    background: linear-gradient(90deg, rgba(31,127,196,0.18), rgba(31,127,196,0.06));
    border-radius: 4px;
  }
  .sign-off .role { font-size: 9.4px; }

  .contact {
    position: absolute; left: 59px; top: 778px;
    font-family: 'Poppins', sans-serif; color: var(--ink); font-size: 10.4px;
    font-style: normal;
  }
  .contact .address { margin-bottom: 4px; }
  .contact-line { display: flex; align-items: center; height: 14.6px; }
  .contact-line svg { width: 9px; height: 9px; margin-right: 12px; flex: none; }

  .footer-block {
    position: absolute; right: 0; bottom: 6px;
    width: 290px; height: 58px;
    background: var(--pink-band);
  }
  .footer-rule {
    position: absolute; left: 0; bottom: 0;
    width: 625px; height: 6px;
    background: var(--ink);
  }

  .motto {
    position: absolute; right: 41px; top: 832px; text-align: right;
    font-family: 'Poppins', sans-serif; font-weight: 600; font-size: 11.6px;
    line-height: 15.5px; color: #fff;
  }
  .motto .highlight { color: var(--pink-soft); font-weight: 500; }
</style>
</head>
<body>
  <main class="letterhead">
    <header class="brand">
      <div class="brand-name">velortis</div>
      <div class="brand-tagline">DENTISTRY &amp; ORTHODONTICS</div>
    </header>

    <section class="letter-body">
      <p class="salutation">Dear Sir,</p>
      <p class="paragraph">Lorem Ipsum is simply dummy text of the printing and typesetting industry. Lorem Ipsum has been the industry's standard dummy text ever since the 1500s, when an unknown printer took a galley of type and scrambled it to make a type specimen book. It has survived not only five centuries, but also the leap into electronic typesetting, remaining essentially unchanged. It was popularised in the 1960s with the release of Letraset sheets containing Lorem Ipsum passages, and more recently with desktop publishing software like Aldus PageMaker including versions of Lorem Ipsum.</p>
      <p class="paragraph">Lorem Ipsum is simply dummy text of the printing and typesetting industry. Lorem Ipsum has been the industry's standard dummy text ever since the 1500s, when an unknown printer took a galley of type and scrambled it to make a type specimen book. It has survived not only five centuries, but also the leap into electronic typesetting, remaining essentially unchanged. It was popularised in the 1960s with the release of Letraset sheets containing Lorem Ipsum passages, and more recently with desktop publishing software like Aldus PageMaker including versions of Lorem Ipsum.</p>
      <p class="paragraph">Lorem Ipsum is simply dummy text of the printing and typesetting industry. Lorem Ipsum has been the industry's standard dummy text ever since the 1500s, when an unknown printer took a galley of type and scrambled it to make a type specimen book.</p>
    </section>

    <section class="sign-off">
      <p class="name-label">Your Name</p>
      <div class="signature" role="img" aria-label="Handwritten signature of Marcus Trelane"></div>
      <p class="role">CEO &nbsp;|&nbsp; Owner</p>
    </section>

    <address class="contact">
      <p class="address">Shop 9, 42 Marrow Lane Karratha WA 6714</p>
      <p class="contact-line">
        <svg viewBox="0 0 10 10" aria-hidden="true"><path d="M1 4 C1 2 9 2 9 4 L7 4.6 L6.4 3.6 L3.6 3.6 L3 4.6 Z M2.5 5 L7.5 5 L8.5 8.5 L1.5 8.5 Z" fill="var(--pink-light)"/></svg>
        (08) 9000 4821
      </p>
      <p class="contact-line">
        <svg viewBox="0 0 10 10" aria-hidden="true"><rect x="0.5" y="2" width="9" height="6.5" fill="var(--pink-light)"/><path d="M0.5 2 L5 5.6 L9.5 2" stroke="#fff" stroke-width="0.9" fill="none"/></svg>
        hello@velortis.com.au
      </p>
      <p class="contact-line">
        <svg viewBox="0 0 10 10" aria-hidden="true"><circle cx="5" cy="5" r="4" fill="var(--pink-light)"/><path d="M1 5 H9 M5 1 C3 3.5 3 6.5 5 9 M5 1 C7 3.5 7 6.5 5 9" stroke="#fff" stroke-width="0.6" fill="none"/></svg>
        <span>velortis.com.au</span>
      </p>
    </address>

    <div class="footer-block" aria-hidden="true"></div>
    <div class="footer-rule" aria-hidden="true"></div>

    <p class="motto">Life is short. <span class="highlight">SMILE</span><br>while you still have teeth.</p>
  </main>
</body>
</html>
```